Dental practice logo either "Dental Lumora Centre" or "Dental Lumora Centre"

Dental practice with either of the logos mentioned above as we haven't decided on the name depends on which one looks better. Our motto of the practice is to create beautiful smiles and perform general dentistry.
Dr Oskar Velindre
47 Marlowby Road
Deeragun
Queensland 4814 and also the contact number, email address and website.
On the backside of the card it should be about the next appointment and also mention on the bottom" If unable to keep an appointment kindly give 24 hours notice otherwise a fee will be charged for the time reserved.
Reason: As it may take longer to design
We want the business card only on the dental practice named Dental Lumora Centre and with a caption underneath the practice name as "Townsville's home of dentistry"
Target Market(s)
dental patients and general population who want beautiful smile
Industry/Entity Type
Dental
Look and feel
Each slider illustrates characteristics of the customer's brand and the style your logo design should communicate.

```html
<!DOCTYPE html>
<html lang="en">
<head>
<meta charset="utf-8">
<title>Dental Lumora Centre – Business Card</title>
<link href="https://fonts.googleapis.com/css2?family=Open+Sans:wght@400;600;700;800&display=swap" rel="stylesheet">
<style>
  :root {
    --bg: #8f8f8f;
    --card: #ffffff;
    --ink: #2b2b2b;
    --ink-soft: #555555;
    --rule: #c9c9c9;
    --orange: #f26a21;
    --orange-light: #f9a13a;
    --red: #e8402a;
  }
  * { box-sizing: border-box; margin: 0; padding: 0; }
  html, body { width: 1200px; height: 894px; overflow: hidden; }
  body {
    background: var(--bg);
    font-family: "Open Sans", Arial, sans-serif;
    color: var(--ink);
    position: relative;
  }
  .card {
    position: absolute;
    left: 260px;
    width: 680px;
    height: 389px;
    background: var(--card);
    overflow: hidden;
    box-shadow: 0 8px 24px rgba(0,0,0,.25);
  }
  .card--front { top: 34px; }
  .card--back { top: 471px; }

  .brand {
    position: absolute;
    display: flex;
    align-items: center;
    gap: 14px;
  }
  .brand__dot {
    width: 62px; height: 62px;
    border-radius: 50%;
    background: var(--orange);
    flex: none;
  }
  .brand__name {
    font-weight: 700;
    font-size: 25px;
    line-height: 1.05;
    letter-spacing: .5px;
    text-transform: uppercase;
    color: var(--ink);
  }
  .brand__caption {
    font-size: 12px;
    font-weight: 400;
    letter-spacing: 1px;
    color: var(--ink-soft);
    margin-top: 5px;
  }
  .card--front .brand { left: 96px; top: 36px; }
  .card--back .brand { left: 200px; top: 30px; }

  .accent {
    position: absolute;
    background: linear-gradient(135deg, var(--orange-light), var(--orange) 55%, var(--red));
  }
  .card--front .accent { left: 0; top: 150px; width: 70px; height: 64px; }
  .card--back .accent { right: 0; top: 186px; width: 28px; height: 62px; }

  .person { position: absolute; left: 96px; top: 156px; }
  .person__name {
    font-weight: 800;
    font-size: 26px;
    letter-spacing: .5px;
    text-transform: uppercase;
    line-height: 1.05;
  }
  .person__role {
    font-weight: 400;
    font-size: 12px;
    letter-spacing: 5px;
    text-transform: uppercase;
    color: var(--ink-soft);
    margin-top: 4px;
  }

  .contacts {
    position: absolute;
    left: 400px;
    top: 248px;
    list-style: none;
  }
  .contacts li {
    display: flex;
    align-items: flex-start;
    gap: 10px;
    font-size: 12.5px;
    font-weight: 600;
    line-height: 1.25;
    margin-bottom: 9px;
  }
  .contacts svg { width: 15px; height: 15px; flex: none; fill: var(--ink); margin-top: 1px; }

  .appointment {
    position: absolute;
    left: 70px;
    right: 70px;
    top: 118px;
  }
  .appointment__title {
    font-weight: 700;
    font-size: 15px;
    letter-spacing: 3px;
    text-transform: uppercase;
    margin-bottom: 14px;
  }
  .appointment__row {
    display: flex;
    gap: 30px;
    margin-bottom: 14px;
  }
  .appointment__field {
    flex: 1;
    display: flex;
    align-items: flex-end;
    gap: 8px;
    font-size: 12.5px;
    font-weight: 600;
  }
  .appointment__line {
    flex: 1;
    border-bottom: 1px solid var(--rule);
    height: 16px;
  }

  .socials {
    position: absolute;
    left: 70px;
    right: 70px;
    top: 266px;
    display: flex;
    justify-content: space-between;
    list-style: none;
  }
  .socials li {
    display: flex;
    align-items: center;
    gap: 10px;
    font-size: 13px;
    color: var(--ink-soft);
  }
  .socials__mark {
    width: 18px; height: 18px;
    background: var(--ink);
    border-radius: 3px;
  }

  .notice {
    position: absolute;
    left: 70px;
    right: 70px;
    bottom: 28px;
    font-size: 11px;
    line-height: 1.45;
    color: var(--ink-soft);
    text-align: center;
  }
</style>
</head>
<body>

  <section class="card card--front">
    <div class="brand">
      <span class="brand__dot"></span>
      <div>
        <p class="brand__name">Dental Lumora<br>Centre</p>
        <p class="brand__caption">Townsville's home of dentistry</p>
      </div>
    </div>
    <div class="accent"></div>
    <div class="person">
      <p class="person__name">Dr Oskar Velindre</p>
      <p class="person__role">General Dentist</p>
    </div>
    <ul class="contacts">
      <li>
        <svg viewBox="0 0 16 16"><path d="M8 1 0 8h2v7h4v-5h4v5h4V8h2z"/></svg>
        <span>47 Marlowby Road<br>Deeragun, Queensland 4814</span>
      </li>
      <li>
        <svg viewBox="0 0 16 16"><path d="M8 0a8 8 0 1 0 0 16A8 8 0 0 0 8 0zm0 1.5c.9 0 2 1.8 2.3 5H5.7C6 3.3 7.1 1.5 8 1.5zM1.6 7.3h2.6c0 .2 0 .5 0 .7s0 .5 0 .7H1.6a6.4 6.4 0 0 1 0-1.4zm4 0h4.8a10 10 0 0 1 0 1.4H5.6a10 10 0 0 1 0-1.4zm6.2 0h2.6a6.4 6.4 0 0 1 0 1.4h-2.6zM8 14.5c-.9 0-2-1.8-2.3-5h4.6c-.3 3.2-1.4 5-2.3 5z"/></svg>
        <span>www.dentallumora.com.au</span>
      </li>
      <li>
        <svg viewBox="0 0 16 16"><path d="M0 3h16v1L8 9 0 4zm0 2.5 8 5 8-5V13H0z"/></svg>
        <span>smile@dentallumora.com.au</span>
      </li>
      <li>
        <svg viewBox="0 0 16 16"><path d="M3.6.8 6 3.5 4.6 5.4c.8 2 2.6 3.9 4.7 4.8l1.7-1.6 2.8 2.3-1.2 2.6C6.8 13.5 1.6 8.6 1.4 2.4z"/></svg>
        <span>07 5550 1482</span>
      </li>
    </ul>
  </section>

  <section class="card card--back">
    <div class="brand">
      <span class="brand__dot"></span>
      <div>
        <p class="brand__name">Dental Lumora<br>Centre</p>
        <p class="brand__caption">Townsville's home of dentistry</p>
      </div>
    </div>
    <div class="appointment">
      <p class="appointment__title">Your next appointment</p>
      <div class="appointment__row">
        <div class="appointment__field">Name<span class="appointment__line"></span></div>
      </div>
      <div class="appointment__row">
        <div class="appointment__field">Date<span class="appointment__line"></span></div>
        <div class="appointment__field">Time<span class="appointment__line"></span></div>
      </div>
    </div>
    <ul class="socials">
      <li><span class="socials__mark"></span>dentallumora</li>
      <li><span class="socials__mark"></span>@dentallumora</li>
      <li><span class="socials__mark"></span>dentallumora</li>
    </ul>
    <div class="accent"></div>
    <p class="notice">If unable to keep an appointment kindly give 24 hours notice,<br>otherwise a fee will be charged for the time reserved.</p>
  </section>

</body>
</html>
```